Website Design for Videographer

I am looking to update my website - www.brinolvaske.com. I am a wedding videographer who specialises in natural and documentary videography.

The website will be built by my designer using the Wordpress Plinthworx framework.

Requirements;
I want the website to have a clean white look mixed in with video footage.
Needs to be classy. At the moment my website uses a lot of Gold. On the new look I DO NOT want gold.

Need a web and mobile design for the following 12 pages;

* Home page (need to have example videos and text)
* About (this is about me and my service)
* Videos (examples of my work)
* Testimonials
* Packages
* Contact
* Content (this is to show social media content that I am making in a vertical format and advertise this service).
* Blog (index page for blog)
* Blog pages (individual pages for blog content)
* Wedding Venues Index Page (https://brinolvaske.com/north-east-wedding-venues/)
* Individual venue pages (https://brinolvaske.com/north-east-wedding-venues/marlow-tendle-lodge-wedding-videos/) - Needs to show videos, photos, text as is on the current page.
* Venue Tours (https://brinolvaske.com/wedding-venue-tours/)

My current logo is attached however on the website I want to go for a black and white style for it.

Example styles I like however must not be copied.
https://joswelbrant.co.uk/about/
https://oakandripple.co.uk/ (if done in white)
https://tumblemothpictures.co.uk/

Target Market(s)

Couples getting married aged 25-35

Industry/Entity Type

Weddings

Number of Pages Required

5+ page

Font styles to use
Sans Serif

Requirements
Must have
• A classy look, black and white, use videos and photos.
Should not have
• Gold colour

```html
<!DOCTYPE html>
<html lang="en">
<head>
<meta charset="utf-8">
<title>Brin Olvaske Wedding Films – North East Wedding Videographer</title>
<link rel="stylesheet" href="https://fonts.googleapis.com/css2?family=Jost:wght@400;500;600&display=swap">
<style>
:root{
  --black:#0b0b0b;
  --ink:#1a1a1a;
  --text:#3c3c3c;
  --white:#ffffff;
  --mist:#f2f2f2;
  --line:#d8d8d8;
  --grey-dark:#2a2623;
}
*{box-sizing:border-box;margin:0;padding:0}
html,body{width:1200px;height:5391px;overflow:hidden}
body{font-family:'Jost',sans-serif;color:var(--text);background:var(--white);position:relative}
section,header,footer{position:absolute;left:0;width:1200px}
h1,h2,h3{font-family:'Jost',sans-serif;font-weight:500;text-transform:uppercase;color:var(--ink);letter-spacing:1px;line-height:1.1}
p{font-size:12.5px;line-height:2;color:var(--text)}
.media{position:absolute;display:block}
.play{position:absolute;width:60px;height:60px;border-radius:50%;background:var(--white);left:50%;top:50%;transform:translate(-50%,-50%)}
.play::after{content:"";position:absolute;left:25px;top:20px;border-left:15px solid var(--black);border-top:10px solid transparent;border-bottom:10px solid transparent}
.inner-frame{position:absolute;inset:16px;border:2px solid var(--white)}

/* header */
.site-header{top:0;height:80px;background:var(--black);display:flex;align-items:center}
.brand{position:absolute;left:144px;top:30px;color:var(--white);font-size:15px;font-weight:500;letter-spacing:3px;display:flex;align-items:center;gap:10px}
.brand i{width:10px;height:10px;background:var(--white);display:block}
.nav{position:absolute;left:390px;top:32px;display:flex;gap:44px}
.nav a{color:var(--white);font-size:13px;font-weight:500;text-decoration:none;letter-spacing:.5px;text-transform:uppercase;position:relative}
.nav a.active::after{content:"";position:absolute;left:0;right:0;bottom:-10px;height:2px;background:var(--white)}

/* hero */
.hero{top:80px;height:562px;background:linear-gradient(180deg,#3a3633 0%,#5a534c 45%,#2c2825 100%)}
.hero-title{position:absolute;top:215px;width:100%;text-align:center;color:var(--white);font-size:42px;line-height:1;letter-spacing:2px}
.hero-sub{position:absolute;top:318px;width:100%;text-align:center;color:var(--white);font-size:15px;font-weight:500;letter-spacing:1px}
.circle-arrow{position:absolute;width:66px;height:66px;border-radius:50%;background:rgba(255,255,255,.35);top:258px}

/* intro */
.intro{top:642px;height:574px}
.intro .media{left:144px;top:90px;width:436px;height:373px;background:linear-gradient(160deg,#6b5a46,#3b3028 60%,#8a7a66)}
.intro-copy{position:absolute;left:602px;top:83px;width:455px}
.intro-copy h2{font-size:36px;margin-bottom:16px}
.intro-copy p{margin-bottom:22px;text-align:justify}
.btn{display:inline-block;background:var(--black);color:var(--white);font-size:13px;font-weight:500;padding:12px 22px;text-transform:uppercase;letter-spacing:.5px}

/* award */
.award{top:1216px;height:442px;background:linear-gradient(120deg,#1c1a19,#2e2a27 50%,#141312)}
.award h2{position:absolute;left:144px;top:90px;color:var(--white);font-size:38px}
.award p{position:absolute;left:144px;top:176px;width:642px;color:#e8e8e8;text-align:justify}
.award-badge{position:absolute;left:850px;top:73px;width:205px;height:260px;background:linear-gradient(135deg,#b8b8b8,#8d8d8d)}
.award-badge span{position:absolute;left:70px;top:25px;width:65px;height:70px;background:var(--black)}

/* natural */
.natural{top:1658px;height:582px}
.natural-box{position:absolute;left:121px;top:138px;width:500px;height:293px;background:var(--mist);padding:24px 24px 0 24px}
.natural-box h2{font-size:36px;margin-bottom:16px}
.natural-box p{text-align:justify;font-size:12px}
.natural .media{left:620px;top:94px;width:435px;height:375px;background:linear-gradient(140deg,#9c8258,#6e5a3b 60%,#a58c60)}

/* amazing */
.amazing{top:2240px;height:360px;background:linear-gradient(90deg,#2f2b28,#4a4440 50%,#2a2624)}
.amazing h2{position:absolute;top:110px;width:100%;text-align:center;color:var(--white);font-size:38px}
.amazing p{position:absolute;left:270px;top:162px;width:660px;text-align:center;color:#eee}

/* day */
.day{top:2600px;height:688px;background:linear-gradient(180deg,#9db0a6 0%,#6f8669 45%,#4e5f45 100%)}
.day-box{position:absolute;left:224px;top:62px;width:751px;height:369px;background:var(--white);padding:12px}
.day-box .bordered{border:2px solid var(--ink);height:100%;padding:22px 30px 0;text-align:center}
.day-box h2{font-size:36px;margin-bottom:18px}
.day-box p{font-size:12px;margin-bottom:18px}

/* relive */
.relive{top:3288px;height:618px}
.tabs{position:absolute;left:121px;top:91px;width:348px}
.tabs li{list-style:none;font-size:14px;font-weight:500;color:var(--ink);text-transform:uppercase;padding:10px 22px;line-height:1.5;margin-bottom:6px}
.tabs li.on{background:var(--black);color:var(--white);padding:12px 22px}
.relive-copy{position:absolute;left:511px;top:92px;width:545px;text-align:justify}
.relive .media{left:511px;top:257px;width:545px;height:258px;background:linear-gradient(120deg,#050505,#262320 50%,#050505)}

/* north east */
.northeast{top:3906px;height:408px;background:linear-gradient(180deg,#3c4744,#2d3832 60%,#22291f)}
.northeast .inner-frame{inset:25px 27px 27px 27px;border-width:3px}
.northeast h2{position:absolute;top:136px;width:100%;text-align:center;color:var(--white);font-size:56px;line-height:1.22}

/* videos */
.videos{top:4314px;height:607px}
.videos h2{position:absolute;top:80px;width:100%;text-align:center;font-size:38px}
.card{position:absolute;top:151px;width:283px;height:351px}
.card .label{position:absolute;bottom:20px;width:100%;text-align:center;color:var(--white);font-size:16px;font-weight:500}
.chev{position:absolute;top:320px}

/* footer */
.site-footer{top:4921px;height:470px;background:var(--black);color:var(--white)}
.footer-brand{position:absolute;left:195px;top:177px;font-size:24px;letter-spacing:6px;font-weight:500;display:flex;align-items:center;gap:14px}
.footer-brand i{width:16px;height:16px;background:var(--white);display:block}
.footer-links h3{position:absolute;left:533px;top:80px;color:var(--white);font-size:22px}
.footer-links .rule{position:absolute;left:533px;top:117px;width:475px;height:1px;background:var(--white)}
.footer-links ul{position:absolute;top:136px;list-style:none}
.footer-links li{font-size:12px;line-height:22.5px;color:var(--white)}
.footer-links li::before{content:"»";margin-right:20px}
.contact-row{position:absolute;top:300px;display:flex;align-items:center;gap:16px;font-size:14px}
.ico{width:38px;height:38px;background:var(--white);display:flex;align-items:center;justify-content:center}
.footer-rule{position:absolute;left:144px;top:365px;width:912px;height:1px;background:#444}
.copyright{position:absolute;top:392px;width:100%;text-align:center;font-size:12px}
.social{position:absolute;top:432px;left:542px;display:flex;gap:22px;align-items:center}
.social span{width:14px;height:14px;border-radius:50%;background:var(--white)}
.social span.big{width:28px;height:28px}
</style>
</head>
<body>

<header class="site-header">
  <div class="brand"><i></i>BRIN OLVASKE</div>
  <nav class="nav">
    <a class="active">Home</a><a>About</a><a>Videos</a><a>Testimonials</a><a>Packages</a><a>Blog</a><a>Contact</a>
  </nav>
</header>

<section class="hero" role="img" aria-label="Bride and groom walking through guests throwing confetti after the ceremony">
  <h1 class="hero-title" style="color:var(--white)">North East Wedding<br>Videographer</h1>
  <div class="hero-sub">BRIN OLVASKE</div>
  <div class="circle-arrow" style="left:78px"><svg width="66" height="66" viewBox="0 0 66 66"><path d="M37 23 27 33 37 43" fill="none" stroke="#111" stroke-width="3"/></svg></div>
  <div class="circle-arrow" style="right:78px"><svg width="66" height="66" viewBox="0 0 66 66"><path d="M29 23 39 33 29 43" fill="none" stroke="#111" stroke-width="3"/></svg></div>
</section>

<section class="intro">
  <div class="media" role="img" aria-label="Wedding ceremony in a rustic barn with guests seated either side"><div class="inner-frame"></div><span class="play"></span></div>
  <div class="intro-copy">
    <h2>Stunning North<br>East Wedding Films</h2>
    <p>A trusted and acclaimed North East wedding videographer who has more than 25 years of videography experience.</p>
    <p>From beautiful barns and luxurious country hotels to sun-drenched Greek Islands and ancient Italian abbeys, he has filmed all kinds of unforgettable weddings.</p>
    <p>If you're looking for a highly experienced wedding videographer who focuses on your story, the 'goosebump' moments and the emotions filling the room as you entertain your guests, then get in touch with Brin today.</p>
    <span class="btn">Watch Films</span>
  </div>
</section>

<section class="award" role="img" aria-label="Bride and groom leaving under falling confetti, darkened">
  <h2 style="color:var(--white)">Vowline Wedding<br>Awards 2024 Winner</h2>
  <p>I'm honoured to have been the only wedding videographer from the North East to win the Vowline Wedding Awards 2024. This award represents more to me than a simple pat on the back; it's evidence of the incredible moments I've recorded for couples on their wedding day. The fact that this victory is entirely the result of the votes and encouraging remarks from the couples I've had the honour of working with makes it even more noteworthy. What really sealed the deal for me on this award was their satisfaction and the memories we've made together.</p>
  <div class="award-badge" role="img" aria-label="Award winner badge"><span></span></div>
</section>

<section class="natural">
  <div class="natural-box">
    <h2>Wedding Videography<br>for Natural Moments</h2>
    <p>My approach to wedding videography is straightforward: I let you and your guests enjoy the pleasure, love, and festivities of the day. The focus will be on capturing the spontaneous, real interactions that make your wedding so unique. When you look back on your wedding day, I want you to remember the genuine smiles, genuine laughing, and spontaneous moments of emotion that you might have missed in the flurry of events.</p>
  </div>
  <div class="media" role="img" aria-label="Aerial view of a couple lying in a golden wheat field"><div class="inner-frame"></div><span class="play"></span></div>
</section>

<section class="amazing" role="img" aria-label="Guests throwing confetti over the couple">
  <h2 style="color:var(--white)">Amazing Weddings</h2>
  <p>It's an honour to work as a wedding videographer in the North East of England. It's truly like living the dream. Imagine, I get to be a part of people's best days, capturing the moments that make it all so memorable. I live for the delight on a bride's face as she says 'I do' or a grandfather breaking a move on the dance floor.</p>
</section>

<section class="day" role="img" aria-label="Couple driving a white vintage convertible along a countryside road">
  <div class="day-box"><div class="bordered">
    <h2>Your wedding day is the most<br>important day of your life…</h2>
    <p>The celebration of your love story… and you'll want to remember it for the rest of your lives.</p>
    <p>Your wedding film is the best way to keep this day alive forever … a newlywed's gift that keeps giving … an infinite reminder of those special moments and memories.</p>
    <p>Everything about your wedding day belongs to you, the couple. Your story. Your vibe. Your friends and family. Your pre-wedding jitters. Your tears. Your laughter. Your vows. Your excitement. Your first dance. Everything. And I'm passionate about creating a wedding film that captures the very essence of your day and turning it into a family heirloom you'll treasure forever.</p>
  </div></div>
</section>

<section class="relive">
  <ul class="tabs">
    <li class="on">Relive those wedding moments<br>over and over again</li>
    <li>Emily loves her wedding video</li>
    <li>Luxury County Durham wedding<br>video</li>
    <li>Wedding dress reveals</li>
  </ul>
  <p class="relive-copy">The nicest part of being a videographer is hearing about the emotional impact of my wedding videos on couples. Your wedding day goes by so quickly, and there are moments you'll regret missing. This is when I step in. I'm capturing candid videos of your nan wiping away a tear or your tiny cousin going crazy on the dance floor while you're reciting your vows or laughing with your friends. These are the things you didn't realise happened until you pressed 'play'.</p>
  <div class="media" role="img" aria-label="Couple embracing in low light, film title card"><span class="play"></span></div>
</section>

<section class="northeast" role="img" aria-label="Aerial view of a countryside church among green fields">
  <div class="inner-frame"></div>
  <h2 style="color:var(--white)">I Love<br>The North East</h2>
</section>

<section class="videos">
  <h2>Wedding Videos</h2>
  <svg class="chev" style="left:56px" width="18" height="30" viewBox="0 0 18 30"><path d="M14 3 3 15 14 27" fill="none" stroke="#111" stroke-width="2.5"/></svg>
  <div class="card" style="left:144px;background:linear-gradient(160deg,#8a8d8a,#4a4c4a)" role="img" aria-label="Groom and bride outside a country house"><span class="play"></span><div class="label">Harrow Fell Lodge Wedding</div></div>
  <div class="card" style="left:458px;background:linear-gradient(170deg,#a9bfd0,#6b8a6a 55%,#4f6b5f)" role="img" aria-label="Riverside town seen from above"><span class="play"></span><div class="label">Durham Celebration</div></div>
  <div class="card" style="left:772px;background:linear-gradient(160deg,#c9c6c0,#6d6a65)" role="img" aria-label="Couple sharing a kiss by a stone arch"><span class="play"></span><div class="label">Marlow Tendle Lodge Love</div></div>
  <svg class="chev" style="right:56px" width="18" height="30" viewBox="0 0 18 30"><path d="M4 3 15 15 4 27" fill="none" stroke="#111" stroke-width="2.5"/></svg>
</section>

<footer class="site-footer">
  <div class="footer-brand"><i></i>BRIN OLVASKE</div>
  <div class="footer-links">
    <h3 style="color:var(--white)">Links</h3>
    <div class="rule"></div>
    <ul style="left:535px">
      <li>FAQ's</li><li>North East Wedding Venues</li><li>Commercial Videography</li><li>Newcastle Wedding Videographer</li><li>Free Speeches Guide</li><li>Northumberland Wedding Videos</li>
    </ul>
    <ul style="left:813px">
      <li>Blog</li><li>North Yorkshire Weddings</li><li>Ios Island Weddings</li><li>Wedding Venue Tours</li><li>Lake District Wedding Videos</li><li>Durham Wedding Videographer</li>
    </ul>
  </div>
  <div class="contact-row" style="left:383px">
    <span class="ico"><svg width="18" height="14" viewBox="0 0 18 14"><rect x="1" y="1" width="16" height="12" fill="none" stroke="#111" stroke-width="1.6"/><path d="M1 1 9 8 17 1" fill="none" stroke="#111" stroke-width="1.6"/></svg></span>films@brinolvaske.com
  </div>
  <div class="contact-row" style="left:656px">
    <span class="ico"><svg width="16" height="16" viewBox="0 0 16 16"><path d="M3 1h3l1.5 4-2 1.3a9 9 0 0 0 4.2 4.2L11 8.5l4 1.5v3a2 2 0 0 1-2 2A13 13 0 0 1 1 3a2 2 0 0 1 2-2z" fill="#111"/></svg></span>07700 900 312
  </div>
  <div class="footer-rule"></div>
  <div class="copyright">Copyright 2024 © Brin Olvaske Wedding Films Limited. All Rights Reserved</div>
  <div class="social"><span></span><span class="big"></span><span></span></div>
</footer>

</body>
</html>
```